E learning Platform for privacy

Current website is as below and its more of a shell.
I need someone to take the text and content and design it properly.
https://study.vornaquill.com/

After that, design has to be implemented with elementor and wordpress
https://elementor.com/

```html
<!DOCTYPE html>
<html lang="en">
<head>
<meta charset="utf-8">
<title>Vornaquill Learning Centre</title>
<link href="https://fonts.googleapis.com/css2?family=Poppins:wght@300;400;500;600&family=Oswald:wght@600;700&display=swap" rel="stylesheet">
<style>
:root{
  --orange:#ee8a25;
  --orange-deep:#f05a23;
  --orange-soft:#f4a24b;
  --ink:#2a2a2a;
  --text:#555;
  --muted:#8a8a8a;
  --line:#e6e6e6;
  --dark:#262626;
  --white:#fff;
}
*{box-sizing:border-box;margin:0;padding:0}
html,body{width:1200px;height:5000px;overflow:hidden;background:var(--white)}
body{font-family:"Poppins",sans-serif;color:var(--text);position:relative}
.abs{position:absolute}
.accent{color:var(--orange)}

/* top bar + hero */
.topbar{left:0;top:0;width:1200px;height:40px;background:var(--orange);color:var(--white);font-size:15px;display:flex;justify-content:flex-end;align-items:center;padding-right:76px;gap:10px;z-index:3}
.topbar .phone-dot{width:26px;height:26px;border-radius:50%;background:var(--orange-deep);display:flex;align-items:center;justify-content:center}
.hero{left:0;top:40px;width:1200px;height:660px;background:linear-gradient(110deg,#4a5560 0%,#6d6f70 35%,#8a7d70 60%,#3b3d40 100%)}
.hero-curve{left:0;top:0;width:1200px;height:700px;z-index:1}
.brand{left:78px;top:56px;z-index:2;display:flex;align-items:center;gap:10px;font-size:30px;font-weight:500;color:var(--orange);letter-spacing:1px}
.brand .mark{width:18px;height:18px;border-radius:50%;background:var(--orange)}
.nav{left:476px;top:70px;z-index:2;display:flex;align-items:center;gap:30px;font-size:14px;color:var(--white);text-transform:uppercase}
.nav .active,.nav .login{color:var(--orange)}
.nav .register{background:var(--orange-deep);padding:10px 18px;border-radius:22px}
.hero-title{left:743px;top:238px;z-index:2;font-family:"Oswald",sans-serif;font-weight:700;font-size:56px;line-height:52px;color:var(--white)}
.hero-sub{left:747px;top:356px;z-index:2;color:var(--white);font-size:16px;line-height:24px;width:330px}
.btn{background:var(--orange-deep);color:var(--white);border-radius:26px;font-size:17px;text-transform:uppercase;display:inline-block}
.hero-btn{left:747px;top:420px;z-index:2;padding:12px 28px}
.arrow{width:44px;height:44px;border-radius:50%;background:var(--orange-deep);z-index:2;display:flex;align-items:center;justify-content:center}

/* welcome */
.welcome-photo{left:145px;top:766px;width:330px;height:330px;border-radius:50%;background:linear-gradient(150deg,#c9b7a5,#8a6b54 55%,#d9d3cb)}
.welcome-badge{left:343px;top:1026px;width:128px;height:128px;border-radius:50%;background:var(--orange);border:5px solid var(--white);box-shadow:0 0 0 3px var(--orange);display:flex;align-items:center;justify-content:center}
.welcome-title{left:553px;top:760px;font-size:38px;font-weight:300;color:var(--ink);line-height:54px;white-space:nowrap}
.welcome-text{left:557px;top:888px;width:500px;font-size:14px;line-height:27px;color:var(--muted)}
.stat{top:1044px;width:155px;height:164px;background:var(--white);box-shadow:0 2px 12px rgba(0,0,0,.09);text-align:center;padding-top:28px}
.stat b{display:block;font-size:27px;font-weight:600;color:var(--ink);margin-top:14px}
.stat span{font-size:15px;color:var(--text)}

/* featured */
.featured-band{left:0;top:1275px;width:1200px;height:740px}
.section-title{width:1200px;left:0;text-align:center;font-size:40px;font-weight:400;color:var(--ink)}
.featured-title{top:1330px;color:var(--white)}
.course{top:1410px;width:291px;height:416px;background:var(--white)}
.course .img{height:197px}
.course .free{position:absolute;left:115px;top:170px;width:62px;height:62px;border-radius:50%;background:var(--orange-deep);color:var(--white);font-size:15px;display:flex;align-items:center;justify-content:center}
.course h3{margin-top:66px;text-align:center;font-size:19px;font-weight:400;color:var(--ink);line-height:24px;padding:0 20px}
.course .meta{margin-top:20px;padding-left:82px;font-size:14px;color:var(--muted);line-height:30px}
.course .meta i{display:inline-block;width:12px;height:12px;background:var(--orange-deep);border-radius:2px;margin-right:14px;vertical-align:-1px}

/* why */
.why-title{top:2068px;line-height:54px}
.why-text{left:260px;top:2185px;width:680px;text-align:center;font-size:14px;line-height:27px;color:var(--muted)}
.feature{top:2312px;width:160px;text-align:center;font-size:17px;line-height:23px;color:var(--ink)}
.feature .ico{width:94px;height:94px;border-radius:50%;margin:0 auto 18px;background:#f1f1f1;display:flex;align-items:center;justify-content:center}
.feature.on .ico{background:var(--orange-deep)}
.divider{left:150px;top:2522px;width:900px;height:2px;background:var(--line)}
.divider i{position:absolute;left:27px;top:0;width:58px;height:4px;background:var(--orange-deep)}
.why-photo{left:225px;top:2565px;width:750px;height:467px;background:linear-gradient(120deg,#d8d0c2 0%,#b9a78f 35%,#e9e5df 70%,#cfc9c0 100%)}
.roadmap{left:225px;top:3075px;border-left:4px solid var(--orange-deep);padding-left:12px;font-size:29px;line-height:36px;color:var(--ink);font-weight:400}
.roadmap-text{left:500px;top:3078px;width:480px;font-size:14px;line-height:27px;color:var(--muted)}

/* testimonial */
.quote-band{left:0;top:3230px;width:1200px;height:500px}
.quote-title{top:3285px;color:var(--ink)}
.avatar{left:258px;top:3388px;width:170px;height:170px;border-radius:50%;background:linear-gradient(160deg,#e8d8c4,#b89473);border:6px solid var(--white)}
.quote-mark{left:382px;top:3390px;width:40px;height:40px;border-radius:50%;background:var(--orange-deep);color:var(--white);font-size:30px;text-align:center;line-height:48px;font-weight:600}
.quote-text{left:462px;top:3408px;width:510px;font-size:15px;line-height:27px;color:var(--white)}
.client{left:468px;top:3535px;font-size:22px;color:var(--white)}

/* blog */
.blog-title{top:3768px;color:var(--ink)}
.blog-card{left:175px;top:3896px;width:567px;height:340px;background:var(--white);box-shadow:0 2px 16px rgba(0,0,0,.1);padding:44px 52px}
.blog-card h3{font-size:26px;font-weight:400;color:var(--ink)}
.blog-card .date{font-size:13px;color:var(--orange-deep);margin-top:6px}
.blog-card p{font-size:14px;line-height:27px;color:var(--muted);margin-top:22px;width:400px}
.blog-card .more{font-size:17px;color:var(--orange);margin-top:18px;display:block}
.blog-img{left:691px;top:3866px;width:364px;height:291px;background:linear-gradient(135deg,#c3a27c,#e9e6e0 50%,#8d6a4a)}
.dots{left:560px;top:4278px;display:flex;gap:9px}
.dots i{width:11px;height:11px;border-radius:50%;background:#d9d9d9}
.dots i.on{background:var(--orange)}

/* footer */
.footer-shape{left:0;top:4330px;width:1200px;height:670px}
.news-title{left:79px;top:4512px;font-size:33px;color:var(--white);font-weight:400}
.news-text{left:79px;top:4567px;width:540px;font-size:14px;line-height:23px;color:#ddd}
.news-form{left:621px;top:4553px;width:500px;height:56px;border-radius:30px;background:var(--white);border:3px solid var(--orange-deep);overflow:hidden;display:flex}
.news-form span{flex:1;padding:16px 22px;font-size:14px;color:#777}
.news-form b{width:150px;background:var(--orange-deep);color:var(--white);font-weight:400;font-size:17px;display:flex;align-items:center;justify-content:center}
.col{top:4690px;font-size:14px;color:#bbb}
.col h4{font-size:19px;font-weight:400;color:var(--orange);margin-bottom:18px}
.col li{list-style:none;line-height:31px;position:relative;padding-left:18px}
.col li:before{content:"";position:absolute;left:0;top:13px;width:6px;height:6px;border-radius:50%;background:var(--orange)}
.contact li{padding-left:32px}
.contact li:before{width:12px;height:12px;border-radius:2px;top:9px;background:var(--orange-deep)}
.foot-brand{left:893px;top:4750px;display:flex;align-items:center;gap:10px;font-size:30px;font-weight:500;color:var(--orange)}
.foot-brand .mark{width:18px;height:18px;border-radius:50%;background:var(--orange)}
.social{left:908px;top:4830px;display:flex;gap:10px}
.social i{width:38px;height:38px;border-radius:50%;border:2px solid var(--orange)}
.copyright{left:0;top:4955px;width:1200px;text-align:center;font-size:13px;color:#ccc;border-top:1px solid #444;padding-top:14px}
.copyright span{color:var(--orange)}
</style>
</head>
<body>

<!-- header & hero -->
<div class="abs topbar">Call Us On : <span class="phone-dot"><svg width="13" height="13" viewBox="0 0 24 24"><path fill="#fff" d="M6.6 10.8a15 15 0 0 0 6.6 6.6l2.2-2.2c.3-.3.7-.4 1-.2 1.1.4 2.3.6 3.6.6.6 0 1 .4 1 1V20c0 .6-.4 1-1 1A17 17 0 0 1 3 4c0-.6.4-1 1-1h3.5c.6 0 1 .4 1 1 0 1.3.2 2.5.6 3.6.1.3 0 .7-.2 1z"/></svg></span> +1 (800) 555 01 24</div>
<div class="abs hero" role="img" aria-label="Photo of a student writing notes beside a laptop"></div>
<svg class="abs hero-curve" viewBox="0 0 1200 700">
  <path d="M0 380 C150 620 340 690 600 668 C850 645 1040 580 1200 530 L1200 700 L0 700 Z" fill="#fff"/>
  <path d="M0 380 C150 620 340 690 600 668 C850 645 1040 580 1200 530" fill="none" stroke="#ee8a25" stroke-width="9"/>
</svg>
<div class="abs brand"><span class="mark"></span>VORNAQUILL</div>
<nav class="abs nav"><span class="active">Home</span><span>Blogs</span><span>Courses</span><span>About Us</span><span>Contact Us</span><span class="login">Login</span><span class="register">Register</span></nav>
<h1 class="abs hero-title">Privacy Practice<br>Mastery</h1>
<p class="abs hero-sub">Largest online e-learning resource for data protection &amp; privacy</p>
<span class="abs btn hero-btn">Get Trained</span>
<div class="abs arrow" style="left:894px;top:566px"><svg width="12" height="18" viewBox="0 0 12 18"><path d="M9 2 2 9l7 7" stroke="#fff" stroke-width="2" fill="none"/></svg></div>
<div class="abs arrow" style="left:948px;top:556px"><svg width="12" height="18" viewBox="0 0 12 18"><path d="m3 2 7 7-7 7" stroke="#fff" stroke-width="2" fill="none"/></svg></div>

<!-- welcome -->
<div class="abs welcome-photo" role="img" aria-label="Photo of smiling students in a classroom"></div>
<div class="abs welcome-badge"><svg width="66" height="60" viewBox="0 0 66 60" fill="none" stroke="#fff" stroke-width="5"><path d="M58 6H14a8 8 0 0 0 0 16h44M58 22H14a8 8 0 0 0 0 16h44M58 38H14a8 8 0 0 0 0 16h44"/></svg></div>
<h2 class="abs welcome-title">Welcome To<br><span class="accent">(VORNAQUILL)</span> Learning Centre</h2>
<p class="abs welcome-text">Lorem Ipsum is simply dummy text of the printing and typesetting industry. Lorem Ipsum has been the industry's standard dummy text ever since the 1500s, when an unknown printer took a galley of type and scrambled it to make a type specimen book. It has survived not only five</p>
<div class="abs stat" style="left:563px"><svg width="56" height="36" viewBox="0 0 56 36" fill="#f05a23"><circle cx="28" cy="9" r="7"/><circle cx="11" cy="13" r="5"/><circle cx="45" cy="13" r="5"/><path d="M16 34c0-9 5-14 12-14s12 5 12 14zM2 34c0-7 4-11 9-11 3 0 5 1 6 3-2 3-3 5-3 8zM54 34c0-7-4-11-9-11-3 0-5 1-6 3 2 3 3 5 3 8z"/></svg><b>6,375</b><span>Enrolled Student</span></div>
<div class="abs stat" style="left:733px"><svg width="50" height="40" viewBox="0 0 50 40" fill="#f05a23"><rect x="2" y="4" width="20" height="14"/><rect x="26" y="4" width="20" height="14"/><circle cx="25" cy="26" r="6"/><path d="M13 40c0-7 5-9 12-9s12 2 12 9z"/></svg><b>144</b><span>Lessons</span></div>
<div class="abs stat" style="left:903px"><svg width="50" height="36" viewBox="0 0 50 36" fill="#f05a23"><rect x="2" y="6" width="32" height="24" rx="4"/><path d="M36 14l12-7v22l-12-7z"/></svg><b>169</b><span>Videos</span></div>

<!-- featured courses -->
<svg class="abs featured-band" viewBox="0 0 1200 740">
  <path d="M0 0H1200V700C1050 735 950 740 820 715C560 660 300 610 0 568Z" fill="#ee8a25"/>
  <path d="M0 568C300 610 560 660 820 715C950 740 1050 735 1200 700" fill="none" stroke="#f05a23" stroke-width="6"/>
</svg>
<h2 class="abs section-title featured-title">Featured Courses</h2>
<article class="abs course" style="left:142px"><div class="img" role="img" aria-label="Photo of a chart printout and a pen" style="background:linear-gradient(135deg,#eef1f4,#b9c6d6 60%,#3c6b4a)"></div><span class="free">FREE</span><h3>How to Scale Social Impact</h3><div class="meta"><i></i>Dec 19,2019<br><i style="border-radius:50%"></i>Mr.Example</div></article>
<article class="abs course" style="left:456px"><div class="img" role="img" aria-label="Photo of hands holding a small plant together" style="background:linear-gradient(135deg,#c9c3bb,#6f6a64 50%,#d4cdc4)"></div><span class="free">FREE</span><h3>Global Social Enrepreneurship</h3><div class="meta"><i></i>Dec 18,2019<br><i style="border-radius:50%"></i>Mr.Example</div></article>
<article class="abs course" style="left:768px"><div class="img" role="img" aria-label="Photo of a man with a headset working on a laptop" style="background:linear-gradient(135deg,#e5e2dc,#9fa7b1 55%,#dcd6ce)"></div><span class="free">FREE</span><h3>Lumora Demonstration Cource</h3><div class="meta"><i></i>Dec 17,2019<br><i style="border-radius:50%"></i>Mr.Example</div></article>

<!-- why -->
<h2 class="abs section-title why-title">Why The <span class="accent">(VORNAQUILL)</span> Learning<br>Centre?</h2>
<p class="abs why-text">Our mission at the Vornaquill Learning Centre is to provide business and job opportunities, as well as to enhance personal and career advancement for data protection / privacy professionals.</p>
<div class="abs feature on" style="left:133px"><div class="ico"><svg width="48" height="44" viewBox="0 0 48 44" fill="none" stroke="#fff" stroke-width="2.5"><circle cx="10" cy="10" r="5"/><circle cx="38" cy="8" r="5"/><path d="M3 42V26h14v16M31 42V22h14v20M17 30h14"/></svg></div>Comprehensive Roadmap</div>
<div class="abs feature" style="left:279px"><div class="ico"><svg width="36" height="46" viewBox="0 0 36 46" fill="none" stroke="#f05a23" stroke-width="2.5"><rect x="3" y="3" width="30" height="40"/><path d="M9 12h18M9 19h18M9 26h10"/><circle cx="24" cy="32" r="5"/></svg></div>Academic &amp; International Certification</div>
<div class="abs feature" style="left:442px"><div class="ico"><svg width="50" height="44" viewBox="0 0 50 44" fill="none" stroke="#f05a23" stroke-width="2.5"><circle cx="25" cy="8" r="5"/><circle cx="9" cy="22" r="5"/><circle cx="41" cy="22" r="5"/><path d="M15 42c0-8 4-12 10-12s10 4 10 12M1 42c0-5 3-8 8-8M49 42c0-5-3-8-8-8"/></svg></div>Network with other peers</div>
<div class="abs feature" style="left:599px"><div class="ico"><svg width="52" height="40" viewBox="0 0 52 40" fill="none" stroke="#f05a23" stroke-width="2.5"><circle cx="14" cy="10" r="6"/><circle cx="32" cy="8" r="5"/><path d="M2 36c0-9 5-14 12-14s12 5 12 14M26 20c6 0 12 4 14 10l10-14"/></svg></div>Operational Perspective</div>
<div class="abs feature" style="left:756px"><div class="ico"><svg width="46" height="46" viewBox="0 0 46 46" fill="none" stroke="#f05a23" stroke-width="2.5"><path d="M4 4l38 38M42 4 4 42M4 4h10M4 4v10M42 42H32M42 42V32M42 4H32M42 4v10M4 42h10M4 42V32"/></svg></div>Modular Approach &amp; Flexibility</div>
<div class="abs feature" style="left:915px"><div class="ico"><svg width="46" height="46" viewBox="0 0 46 46" fill="none" stroke="#f05a23" stroke-width="2.5"><rect x="13" y="13" width="20" height="20"/><path d="M23 3v10M23 33v10M3 23h10M33 23h10"/><circle cx="23" cy="23" r="4"/></svg></div>Business &amp; Job Opportunities</div>
<div class="abs divider"><i></i></div>
<div class="abs why-photo" role="img" aria-label="Photo of a woman working on a laptop in front of a bookshelf"></div>
<h3 class="abs roadmap">Comprehensive<br>Roadmap</h3>
<p class="abs roadmap-text">Our objective is to provide a comprehensive competency roadmap, instead of one-off courses, whether you are a new or experienced officer, or an individual pursuing a career in data protection.</p>

<!-- testimonial -->
<svg class="abs quote-band" viewBox="0 0 1200 500">
  <path d="M0 0H1200V200C1000 320 800 470 560 485C320 495 120 380 0 240Z" fill="#ee8a25"/>
  <path d="M0 240C120 380 320 495 560 485C800 470 1000 320 1200 200" fill="none" stroke="#f05a23" stroke-width="6"/>
</svg>
<h2 class="abs section-title quote-title">What <span style="color:#fff">People</span> Say</h2>
<div class="abs avatar" role="img" aria-label="Portrait photo of a client"></div>
<div class="abs quote-mark">&ldquo;</div>
<p class="abs quote-text">Lorem Ipsum is simply dummy text of the printing and typesetting industry. Lorem Ipsum has been the industry's standard dummy text ever since the 1500s, when an unknown printer took a galley of type and scrambled it to make a type specimen book."</p>
<p class="abs client">&mdash; Client Name</p>
<svg class="abs" style="left:190px;top:3453px" width="14" height="24" viewBox="0 0 14 24"><path d="M12 2 2 12l10 10" stroke="#fff" stroke-opacity=".6" stroke-width="2" fill="none"/></svg>
<svg class="abs" style="left:1026px;top:3453px" width="14" height="24" viewBox="0 0 14 24"><path d="m2 2 10 10L2 22" stroke="#fff" stroke-opacity=".6" stroke-width="2" fill="none"/></svg>

<!-- blog -->
<h2 class="abs section-title blog-title">Latest <span class="accent">Blog</span></h2>
<article class="abs blog-card"><h3>How To Write Blog</h3><p class="date">December 18, 2019 | Posted by vq_admin</p><p>Writing a blog post is a little like driving; you can study the highway code (or read articles telling you how to write a blog post) for months, but nothing can prepare you for the real thing like getting behind the wheel and hitting the open road.</p><span class="more">Read More &#9656;</span></article>
<div class="abs blog-img" role="img" aria-label="Photo of a desk with papers and a laptop seen from above"></div>
<div class="abs dots"><i></i><i class="on"></i><i></i><i></i></div>

<!-- footer -->
<svg class="abs footer-shape" viewBox="0 0 1200 670">
  <path d="M0 165C300 195 650 120 900 40C1000 10 1100 5 1200 20V670H0Z" fill="#262626"/>
  <path d="M0 165C300 195 650 120 900 40C1000 10 1100 5 1200 20" fill="none" stroke="#f05a23" stroke-width="6"/>
</svg>
<h2 class="abs news-title">SignUp For <span class="accent">Newsletter !</span></h2>
<p class="abs news-text">Subscribe now &amp; receive weekly newsletter with educational materials, new courses, interesting posts, popular books &amp; much more!</p>
<div class="abs news-form"><span>Enter Email *</span><b>SUBSCRIBE</b></div>
<div class="abs col" style="left:80px"><h4>Sitemap</h4><ul><li>Home</li><li>Blogs</li><li>Courses</li><li>About Us</li><li>Contact Us</li></ul></div>
<div class="abs col" style="left:346px"><h4>Quick Links</h4><ul><li>Faq</li><li>Terms of Service</li><li>Honor Code</li><li>Privacy Policy</li></ul></div>
<div class="abs col contact" style="left:612px"><h4>Contact Us</h4><ul><li>Eastbrook<br>418 Harbor Lane, Ridgefield,<br>TX 75012, USA</li><li>+1 (800) 555 01 24</li><li>support@study.vornaquill.com</li></ul></div>
<div class="abs foot-brand"><span class="mark"></span>VORNAQUILL</div>
<div class="abs social"><i></i><i></i><i></i><i></i></div>
<p class="abs copyright">&copy;<span>VORNAQUILL LEARNING CENTER</span> &ndash; 2020 All rights reserved.</p>

</body>
</html>
```